Business card for law firm

Need business card for new law firm. Think confident, authoritative, conservative, but not stuffy or old-fashioned.

Contact Information for Business Card

Content for card - logo (uploaded), plus the following:

Paul Whitcombe (larger font)
Managing Partner (larger font, but not as large as name)
Level 9, 7 Ferris Lane
Sydney NSW 2000
Main Tel 02 9364 2710
Direct Tel 02 8472 3159
Email paul@qvlegal.com.au
www.qvlegal.com.au

Letterhead design should include logo plus:
Level 9, 7 Ferris Lane
Sydney NSW 2000
Tel 02 8472 3159
www.qvlegal.com.au

```html
<!DOCTYPE html>
<html lang="en">
<head>
<meta charset="utf-8">
<title>Quayvale Legal – Business Card</title>
<link rel="stylesheet" href="https://fonts.googleapis.com/css2?family=Cormorant+Garamond:wght@500;600&family=Roboto:wght@400;700&display=swap">
<style>
  :root {
    --navy: #001a55;
    --navy-deep: #00164a;
    --navy-light: #0a2466;
    --paper: #e6e6e6;
    --ink: #141414;
    --text: #2b2b2b;
    --backdrop: #9c9c9c;
    --white: #ffffff;
  }
  * { margin: 0; padding: 0; box-sizing: border-box; }
  html, body {
    width: 1200px; height: 1000px; overflow: hidden;
    background: var(--backdrop);
  }
  .card {
    position: absolute; top: 207px;
    width: 352px; height: 586px;
    text-align: center;
  }
  .card--front {
    left: 200px;
    background: linear-gradient(160deg, var(--navy-light) 0%, var(--navy) 45%, var(--navy-deep) 100%);
    color: var(--white);
  }
  .card--back {
    left: 637px;
    background: var(--paper);
    color: var(--text);
    font-family: 'Roboto', Arial, sans-serif;
  }
  .brand { position: absolute; left: 0; right: 0; }
  .brand__square {
    display: block; margin: 0 auto;
    width: 46px; height: 46px;
  }
  .card--front .brand__square { background: var(--white); }
  .card--back .brand__square { background: var(--navy); }
  .brand__name {
    font-family: 'Cormorant Garamond', Georgia, serif;
    font-weight: 600;
    font-size: 42px;
    letter-spacing: 0.04em;
    line-height: 1;
    margin-top: 44px;
  }
  .brand__tag {
    font-family: 'Cormorant Garamond', Georgia, serif;
    font-weight: 500;
    font-size: 16px;
    letter-spacing: 0.62em;
    padding-left: 0.62em;
    line-height: 1;
    margin-top: 8px;
  }
  .card--front .brand { top: 225px; }
  .card--back .brand { top: 62px; color: var(--ink); }
  .card--back .brand__name { margin-top: 40px; }

  .contact { position: absolute; left: 0; right: 0; top: 312px; }
  .contact__name {
    color: var(--navy); font-weight: 700; font-size: 24px; line-height: 28px;
  }
  .contact__role { font-size: 17px; line-height: 22px; }
  .divider {
    width: 56px; height: 2px; background: var(--navy);
    margin: 0 auto;
  }
  .contact__block { font-size: 14px; line-height: 18px; }
  .label, .domain { color: var(--navy); }
  .icons { display: flex; justify-content: center; gap: 6px; margin-top: 24px; }
  .icons svg { width: 11px; height: 11px; }
</style>
</head>
<body>
  <section class="card card--front" aria-label="Card front">
    <div class="brand">
      <span class="brand__square"></span>
      <div class="brand__name">QUAYVALE</div>
      <div class="brand__tag">LEGAL</div>
    </div>
  </section>

  <section class="card card--back" aria-label="Card back">
    <div class="brand">
      <span class="brand__square"></span>
      <div class="brand__name">QUAYVALE</div>
      <div class="brand__tag">LEGAL</div>
    </div>

    <div class="contact">
      <div class="contact__name">PAUL WHITCOMBE</div>
      <div class="contact__role">Managing Partner</div>
      <div class="divider" style="margin-top:12px"></div>
      <div class="contact__block" style="margin-top:12px">
        Level 9, 7 Ferris Lane<br>Sydney NSW 2000
      </div>
      <div class="divider" style="margin-top:13px"></div>
      <div class="contact__block" style="margin-top:12px">
        <span class="label">Main Tel</span> 02 9364 2710<br>
        <span class="label">Direct Tel</span> 02 8472 3159
      </div>
      <div class="icons">
        <svg viewBox="0 0 12 12" aria-hidden="true">
          <circle cx="6" cy="6" r="6" fill="#2f4f8f"/>
          <rect x="2.8" y="3.8" width="6.4" height="4.4" fill="#fff"/>
          <path d="M2.8 3.8 L6 6.4 L9.2 3.8" fill="none" stroke="#2f4f8f" stroke-width="0.8"/>
        </svg>
        <svg viewBox="0 0 12 12" aria-hidden="true">
          <circle cx="6" cy="6" r="5.3" fill="#2f4f8f"/>
          <g fill="none" stroke="#fff" stroke-width="0.7">
            <circle cx="6" cy="6" r="4"/>
            <ellipse cx="6" cy="6" rx="1.7" ry="4"/>
            <path d="M2 6 H10 M2.6 4 H9.4 M2.6 8 H9.4"/>
          </g>
        </svg>
      </div>
      <div class="contact__block" style="margin-top:4px">
        paul@qvlegal.com.au<br>
        www.<span class="domain">qvlegal.com</span>.au
      </div>
    </div>
  </section>
</body>
</html>
```